I need the Scorecard I've developed for my staff to be produced into a visually engaging piece that will encourage the staff to utilize it on a daily basis. I'm thinking it could be 5x7 in size so that it isn't too cumbersome, but I'm open to different layouts.
I have multiple other departments that will need Scorecards created for them as well, but each one will contain task specific questions for each department.

```html
<!DOCTYPE html>
<html lang="en">
<head>
<meta charset="utf-8">
<title>Receptionist Daily Excellence Scorecard</title>
<link href="https://fonts.googleapis.com/css2?family=Poppins:wght@400;500;600;700;800&display=swap" rel="stylesheet">
<style>
:root{
  --magenta:#d3147c;
  --purple:#a0228e;
  --pink-light:#e6cde0;
  --pink-soft:#dca8c8;
  --field:#ebebeb;
  --row-grey:#ececec;
  --ink:#222;
  --indigo:#4b2c7e;
  --backdrop:#666;
  --teal:#1a9fa3;
  --yellow:#f2d40c;
  --pink-dot:#e27ab8;
}
*{box-sizing:border-box;margin:0;padding:0}
html,body{width:1200px;height:1002px;overflow:hidden}
body{background:var(--backdrop);font-family:'Poppins',sans-serif;color:var(--ink);position:relative}
.page{position:absolute;top:162px;width:483px;height:677px;background:#fff}
.page-front{left:98px}
.page-back{left:620px}
.abs{position:absolute;line-height:1}
.field{position:absolute;background:var(--field);border-radius:10px}

.title{left:0;width:100%;top:20px;text-align:center;font-size:27px;font-weight:700;color:var(--magenta);letter-spacing:-.3px}
.banner{position:absolute;left:92px;top:46px;width:299px;height:21px;border-radius:11px;
  background:linear-gradient(90deg,var(--pink-soft),var(--magenta) 60%,var(--purple));
  color:#fff;font-size:11px;font-weight:700;letter-spacing:4px;text-align:center;line-height:21px}
.label{font-size:10px}
.rate-note{font-size:9.5px;line-height:1.15}
.rate-box{position:absolute;width:22px;height:22px;background:var(--pink-light);border-radius:3px}
.rule{position:absolute;height:1px;background:#bbb}

.section{position:absolute;width:207px}
.section-head{font-size:9px;font-weight:700;display:flex;align-items:center;gap:4px;height:12px;margin-bottom:12px;white-space:nowrap}
.num{display:inline-block;width:10px;height:10px;background:var(--magenta);color:#fff;font-size:8px;text-align:center;line-height:10px;border-radius:1px}
.table-head{display:flex;height:21px;padding-left:10px}
.table-head span{font-size:7.5px;text-align:center;line-height:1;display:flex;align-items:center;justify-content:center;border-radius:6px 6px 0 0;margin-right:1px;text-transform:uppercase}
.th-task{width:54px;background:var(--pink-light)}
.th-rate{width:70px;background:var(--magenta);color:#fff}
.th-notes{width:70px;background:var(--pink-light)}
.row{display:flex;overflow:hidden}
.row .task{width:64px;font-size:6.5px;line-height:1.2;padding:2px 4px;display:flex;align-items:center}
.row .task.tiny{font-size:5px;line-height:1.25}
.row .fill{flex:1}
.row.hi .task{background:var(--magenta);color:#fff;font-weight:600}
.row.hi .fill{background:var(--row-grey)}
.row.lo .task{background:var(--row-grey);color:#333}
.row.lo .fill{background:#fff}
.rows{border-radius:0 0 6px 6px;overflow:hidden}

.status-band{position:absolute;left:0;top:0;width:100%;height:42px;
  background:linear-gradient(90deg,var(--pink-soft),var(--magenta) 55%,var(--purple));
  color:#fff;font-size:12px;font-weight:700;text-align:center;padding-top:20px}
.status-box{position:absolute;left:35px;top:42px;width:413px;height:99px;background:var(--field);border-radius:0 0 12px 12px}
.status-item{position:absolute;left:19px;font-size:10px;display:flex;align-items:center;gap:6px;white-space:nowrap}
.dot{width:11px;height:11px;border-radius:50%;flex:none}
.status-item b{color:var(--magenta);font-weight:600}
.heading{font-size:12px;font-weight:700;color:var(--magenta);left:22px}
.heading.indigo{color:var(--indigo)}
.prompt{font-size:10px;left:23px}
.bold-label{font-size:9.5px;font-weight:600;left:22px}
</style>
</head>
<body>

<section class="page page-front">
  <div class="abs title">RECEPTIONIST</div>
  <div class="banner">DAILY EXCELLENCE SCORECARD</div>

  <div class="abs label" style="left:22px;top:78px">Name</div>
  <div class="field" style="left:70px;top:76px;width:253px;height:15px"></div>
  <div class="abs label" style="left:334px;top:78px">Date</div>
  <div class="field" style="left:366px;top:76px;width:92px;height:15px"></div>
  <div class="abs label" style="left:22px;top:98px">Location</div>
  <div class="field" style="left:70px;top:96px;width:388px;height:15px"></div>

  <div class="abs rate-note" style="left:22px;top:122px">Please rate yourself<br>for each task</div>
  <div class="rate-box" style="left:149px;top:121px"></div>
  <div class="abs rate-note" style="left:175px;top:122px">Needs<br>Improvement</div>
  <div class="rate-box" style="left:266px;top:121px"></div>
  <div class="abs rate-note" style="left:293px;top:122px">Meets<br>Expectations</div>
  <div class="rate-box" style="left:378px;top:121px"></div>
  <div class="abs rate-note" style="left:405px;top:128px">Excellent</div>
  <div class="rule" style="left:22px;top:154px;width:436px"></div>

  <div class="section" style="left:23px;top:164px">
    <div class="section-head"><span class="num">1</span>CALL HANDLING &amp; FIRST CALL INTAKE</div>
    <div class="table-head"><span class="th-task">Task</span><span class="th-rate">Self-Rating<br>(1-5)</span><span class="th-notes">Notes or<br>Issues</span></div>
    <div class="rows">
      <div class="row hi" style="height:30px"><div class="task">Answered 90%+ calls within 3 rings</div><div class="fill"></div></div>
      <div class="row lo" style="height:31px"><div class="task">Maintained empathy and professionalism</div><div class="fill"></div></div>
      <div class="row hi" style="height:30px"><div class="task">Accurately completed all First Call fields</div><div class="fill"></div></div>
      <div class="row lo" style="height:31px"><div class="task">Worked within Receptionist role</div><div class="fill"></div></div>
    </div>
  </div>

  <div class="section" style="left:23px;top:357px">
    <div class="section-head"><span class="num">2</span>CALL MANAGEMENT DURING BUSY TIMES</div>
    <div class="table-head"><span class="th-task">Task</span><span class="th-rate">Self-Rating<br>(1-5)</span><span class="th-notes">Notes or<br>Issues</span></div>
    <div class="rows">
      <div class="row hi" style="height:30px"><div class="task">Prioritized urgent vs. non-urgent calls</div><div class="fill"></div></div>
      <div class="row lo" style="height:24px"><div class="task">Hold times under 1 minute</div><div class="fill"></div></div>
      <div class="row hi" style="height:23px"><div class="task">Logged all calls</div><div class="fill"></div></div>
      <div class="row lo" style="height:29px"><div class="task">Requested help if overwhelmed</div><div class="fill"></div></div>
    </div>
  </div>

  <div class="section" style="left:23px;top:519px">
    <div class="section-head"><span class="num">3</span>CALL MANAGEMENT DURING BUSY TIMES</div>
    <div class="table-head"><span class="th-task">Task</span><span class="th-rate">Self-Rating<br>(1-5)</span><span class="th-notes">Notes or<br>Issues</span></div>
    <div class="rows">
      <div class="row hi" style="height:29px"><div class="task">Updated scheduling board</div><div class="fill"></div></div>
      <div class="row lo" style="height:24px"><div class="task">Cross-checked with Red Book</div><div class="fill"></div></div>
      <div class="row hi" style="height:35px"><div class="task">Entered manifold info promptly</div><div class="fill"></div></div>
    </div>
  </div>

  <div class="section" style="left:254px;top:164px">
    <div class="section-head"><span class="num">4</span>CLOTHING &amp; FLOWERS</div>
    <div class="table-head"><span class="th-task">Task</span><span class="th-rate">Self-Rating<br>(1-5)</span><span class="th-notes">Notes or<br>Issues</span></div>
    <div class="rows">
      <div class="row hi" style="height:24px"><div class="task">Clothing sheet completed</div><div class="fill"></div></div>
      <div class="row lo" style="height:24px"><div class="task">Family contact noted on sheet</div><div class="fill"></div></div>
      <div class="row hi" style="height:24px"><div class="task">Floral deliveries logged</div><div class="fill"></div></div>
      <div class="row lo" style="height:34px"><div class="task">Concerns communicated to Care Center</div><div class="fill"></div></div>
      <div class="row hi" style="height:31px"><div class="task">Flower placement verified</div><div class="fill"></div></div>
    </div>
  </div>

  <div class="section" style="left:254px;top:359px">
    <div class="section-head"><span class="num">5</span>DEATH CERTIFICATES</div>
    <div class="table-head"><span class="th-task">Task</span><span class="th-rate">Self-Rating<br>(1-5)</span><span class="th-notes">Notes or<br>Issues</span></div>
    <div class="rows">
      <div class="row hi" style="height:30px"><div class="task">Verified recipient ID &amp; relationship</div><div class="fill"></div></div>
      <div class="row lo" style="height:24px"><div class="task tiny">Confirmed correct documents enclosed</div><div class="fill"></div></div>
      <div class="row hi" style="height:23px"><div class="task">Recipient signed the DC logbook</div><div class="fill"></div></div>
      <div class="row lo" style="height:29px"><div class="task">Suggested proofreading before leaving</div><div class="fill"></div></div>
    </div>
  </div>

  <div class="section" style="left:254px;top:521px">
    <div class="section-head"><span class="num">6</span>ROUTING &amp; MESSAGES</div>
    <div class="table-head"><span class="th-task">Task</span><span class="th-rate">Self-Rating<br>(1-5)</span><span class="th-notes">Notes or<br>Issues</span></div>
    <div class="rows">
      <div class="row hi" style="height:23px"><div class="task">Calls routed appropriately</div><div class="fill"></div></div>
      <div class="row lo" style="height:31px"><div class="task">Messages included all required info</div><div class="fill"></div></div>
      <div class="row hi" style="height:35px"><div class="task">Delivered 95%+ messages in 30 min</div><div class="fill"></div></div>
    </div>
  </div>
</section>

<section class="page page-back">
  <div class="status-band">DAILY STATUS SUMMARY (CIRCLE ONE)</div>
  <div class="status-box">
    <div class="status-item" style="top:16px"><span class="dot" style="background:var(--teal)"></span><span><b>Excellent –</b> All key duties completed, proactive, calm under pressure</span></div>
    <div class="status-item" style="top:39px"><span class="dot" style="background:var(--yellow)"></span><span><b>Satisfactory –</b> Most duties completed, minor follow-up needed</span></div>
    <div class="status-item" style="top:61px"><span class="dot" style="background:var(--pink-dot)"></span><span><b>Needs Support –</b> Missed urgent duties, accuracy or stress issues</span></div>
  </div>

  <div class="abs heading" style="top:155px">DAILY REFLECTION</div>
  <div class="abs prompt" style="top:177px">What went well today?</div>
  <div class="field" style="left:22px;top:195px;width:436px;height:16px"></div>
  <div class="abs prompt" style="top:225px">Any issues or barriers to note?</div>
  <div class="field" style="left:22px;top:248px;width:436px;height:16px"></div>
  <div class="abs prompt" style="top:277px">Support needed from supervisor?</div>
  <div class="field" style="left:22px;top:302px;width:436px;height:16px"></div>

  <div class="abs heading" style="top:336px">STARS &amp; FLAGS (SUPERVISOR USE ONLY)</div>
  <div class="abs heading indigo" style="top:352px">STARS (EXCELLENCE OR ABOVE-AND-BEYOND MOMENTS)</div>
  <div class="field" style="left:22px;top:378px;width:436px;height:16px"></div>
  <div class="abs heading" style="top:412px;left:23px">FLAGS (CONCERNS NEEDING FOLLOW-UP/COACHING)</div>
  <div class="field" style="left:22px;top:436px;width:436px;height:30px;border-radius:15px"></div>

  <div class="abs heading" style="top:483px">MANAGER'S OVERALL RATING</div>
  <div class="abs bold-label" style="top:499px">(Manager: Please rate overall performance on a 1-5 scale)</div>
  <div class="abs bold-label" style="top:515px">Manager Overall Rating (1-5):</div>
  <div class="rule" style="left:172px;top:526px;width:288px"></div>
  <div class="rule" style="left:24px;top:565px;width:436px"></div>

  <div class="abs bold-label" style="top:593px">Receptionist Signature:</div>
  <div class="field" style="left:140px;top:591px;width:318px;height:15px"></div>
  <div class="abs bold-label" style="top:613px">Supervisor Signature:</div>
  <div class="field" style="left:140px;top:611px;width:318px;height:15px"></div>
  <div class="abs bold-label" style="top:633px">Date:</div>
  <div class="field" style="left:52px;top:631px;width:406px;height:15px"></div>
</section>

</body>
</html>
```